Brell Stone Company Business Cards

Front and Back Business Card - logo and text setup - cool design. I need workable photoshop or illustrator files so I can setup each employee card with design that is created
Updates

Hi everyone, thank you for the great entries. Please no more white and blue cards - there are so many already - black and silver only now please. thanks!

Target Market(s)

Construction Industry - Facility Managers

Industry/Entity Type

Construction

Contact Information for Business Card

I really like contemporary simplistic looks - clean neat....not opposed to seeing some black backrounds

Requirements
Must have
• Logo/website address with design on front only - www.brellstone-example.com (logo attached)
• Back:
• Name/Title/Company Address/Phone/email address
Nice to have
• Cool design
Should not have
• Nothing gimmicky like Fire or Water - since we are a Fire Protection company - it has all been done

```html
<!DOCTYPE html>
<html lang="en">
<head>
<meta charset="utf-8">
<title>Brell Stone Company – Business Cards</title>
<link rel="stylesheet" href="https://fonts.googleapis.com/css2?family=Open+Sans:wght@400;600;700;800&display=swap">
<style>
  :root {
    --backdrop: #2a2a2c;
    --card-top: #2b2b2d;
    --card-bottom: #1a1a1b;
    --silver: #c9cacc;
    --silver-bright: #e6e7e9;
    --silver-dim: #8e8f92;
    --rule: #6d6e71;
  }
  * { margin: 0; padding: 0; box-sizing: border-box; }
  html, body {
    width: 1200px;
    height: 874px;
    overflow: hidden;
    background: var(--backdrop);
    font-family: "Open Sans", Arial, sans-serif;
  }
  .sheet {
    width: 1200px;
    height: 874px;
    display: flex;
    flex-direction: column;
    align-items: center;
    justify-content: center;
    gap: 26px;
  }
  .card {
    width: 620px;
    height: 354px;
    border-radius: 18px;
    background: linear-gradient(160deg, var(--card-top), var(--card-bottom));
    position: relative;
    display: flex;
    flex-direction: column;
    align-items: center;
    justify-content: center;
    text-align: center;
  }
  .card-front .company-name {
    font-size: 50px;
    font-weight: 800;
    letter-spacing: -0.5px;
    color: var(--silver);
  }
  .card-back { justify-content: flex-start; padding-top: 150px; }
  .person-name {
    font-size: 24px;
    font-weight: 600;
    letter-spacing: 1px;
    color: var(--silver-bright);
  }
  .person-title {
    font-size: 14px;
    font-weight: 600;
    color: var(--silver);
    margin-top: 1px;
  }
  .divider {
    width: 56px;
    height: 1px;
    background: var(--rule);
    margin: 9px 0;
  }
  .contact-line {
    font-size: 12.5px;
    color: var(--silver-dim);
    line-height: 1.6;
  }
  .contact-line b { font-weight: 700; color: var(--silver); }
  .website {
    font-size: 14px;
    font-weight: 600;
    letter-spacing: 4px;
    color: var(--silver);
    margin-top: 2px;
  }
</style>
</head>
<body>
  <main class="sheet">
    <section class="card card-front" aria-label="Card front">
      <h1 class="company-name">Brell Stone Company</h1>
    </section>

    <section class="card card-back" aria-label="Card back">
      <h2 class="person-name">DANA WHITFIELD</h2>
      <p class="person-title">CEO/Founder</p>
      <div class="divider"></div>
      <p class="contact-line">48 Harbor Point Road, Northvale, NY 10020</p>
      <p class="contact-line"><b>P.</b> (555) 014-2290 <b>F.</b> (555) 014-2291 <b>E.</b> info@brellstone-example.com</p>
      <div class="divider"></div>
      <p class="website">WWW.BRELLSTONE-EXAMPLE.COM</p>
    </section>
  </main>
</body>
</html>
```